Business Card Design Project

We need a business card for a new technology services company. We develop software and implement software packages for our business customers and although we will begin with just one or two service offerings, our service offerings will expand over time. Our name comes from the an author, KL Barrow, and his "idea" was that opportunity should be based on ability and achievement, not on social status.

We would like to see a design that is standard in its size and shape, but stands apart in its dramatic color contrasts. The card should not use too many colors - the colors used in the background should highlight the brilliant blues of the logo (see attachment) to dramatic effect. The background should not be white.

If necessary, you can change the color of the words "KL Barrow", but not the word "Idea".

Card size should be U.S. standard 2 inches by 3.5 inches and provide for 1/8 inch bleed area on each side.

We need a design for both sides of the business card, one side communicating the company logo and contact information, the other side being purely graphical, incorporating the logo but no other information.

Contact Information Required:
Kate Brook
KateBrook@klbarrowvista.com
614-387-2259

Target Market(s)

Business executives

Industry/Entity Type

Software

Requirements
Must have
• It must have the full company logo on one side, and at least the graphic element of the logo on the other. Either that or the full logo on both.
Nice to have
• It would be nice to have a design that could work without needing two different textures. For example, it would be nice if the entire card could be shiny, not just parts of the card.

It would also be nice if texture is something we could add later.
Should not have
• The card should not use the color green.

```html
<!DOCTYPE html>
<html lang="en">
<head>
<meta charset="utf-8">
<title>KL Barrow Vista — Business Card</title>
<link rel="stylesheet" href="https://fonts.googleapis.com/css2?family=Inter:wght@300&family=Tinos:ital,wght@1,700&display=swap">
<style>
  :root {
    --stage: #999999;
    --card: #000000;
    --accent-orange: #ff4e00;
    --accent-cyan: #00c8dc;
    --divider: #8f8f8f;
    --wordmark: #a6a6a6;
    --ink-dark: #000000;
    --ink-light: #ffffff;
  }
  * { margin: 0; padding: 0; box-sizing: border-box; }
  html, body {
    width: 1200px;
    height: 491px;
    overflow: hidden;
    background: var(--stage);
  }
  .stage { position: relative; width: 1200px; height: 491px; }

  .card {
    position: absolute;
    top: 104px;
    width: 495px;
    height: 282px;
    border-radius: 30px;
    background: var(--card);
    overflow: hidden;
  }
  .card--front { left: 72px; }
  .card--back { left: 633px; }

  .brand-mark {
    position: absolute;
    border-radius: 50%;
    background: var(--accent-cyan);
  }
  .wordmark {
    position: absolute;
    font-family: "Inter", Arial, sans-serif;
    font-weight: 300;
    color: var(--wordmark);
    letter-spacing: -1.5px;
    white-space: nowrap;
    line-height: 1;
  }

  .card--front .brand-mark { left: 352px; top: 52px; width: 64px; height: 64px; }
  .card--front .wordmark { left: 60px; top: 126px; font-size: 38px; }

  .divider {
    position: absolute;
    left: 0; right: 0;
    top: 186px;
    height: 4px;
    background: var(--divider);
  }
  .contact-band {
    position: absolute;
    left: 0; right: 0;
    top: 193px;
    bottom: 0;
    background: var(--accent-orange);
  }
  .holder-name {
    position: absolute;
    left: 56px;
    top: 34px;
    font-family: "Tinos", "Times New Roman", serif;
    font-style: italic;
    font-weight: 700;
    font-size: 29px;
    color: var(--accent-cyan);
    white-space: nowrap;
  }
  .contact-list {
    position: absolute;
    left: 252px;
    top: 33px;
    list-style: none;
    font-family: "Tinos", "Times New Roman", serif;
    font-style: italic;
    font-weight: 700;
    font-size: 14px;
    color: var(--ink-dark);
  }
  .contact-list li {
    display: flex;
    align-items: center;
    gap: 5px;
    height: 24px;
    white-space: nowrap;
  }
  .contact-icon { width: 16px; height: 16px; flex: none; }
  .contact-icon--at {
    font-family: Arial, sans-serif;
    font-style: normal;
    font-size: 17px;
    color: var(--accent-cyan);
    width: 16px;
    text-align: center;
  }

  .card--back .brand-mark { left: 360px; top: 100px; width: 76px; height: 76px; }
  .card--back .wordmark { left: 18px; top: 176px; font-size: 44px; }
  .back-email {
    position: absolute;
    left: 0; right: 0;
    top: 255px;
    text-align: center;
    font-family: "Tinos", "Times New Roman", serif;
    font-style: italic;
    font-weight: 700;
    font-size: 16px;
    color: var(--ink-light);
  }
</style>
</head>
<body>
<main class="stage">
  <section class="card card--front" aria-label="Card front">
    <span class="brand-mark"></span>
    <p class="wordmark">KL Barrow Vista</p>
    <div class="divider"></div>
    <div class="contact-band">
      <p class="holder-name">Kate Brook</p>
      <ul class="contact-list">
        <li>
          <svg class="contact-icon" viewBox="0 0 24 24" aria-hidden="true">
            <path fill="#00c8dc" d="M6.6 10.8c1.4 2.8 3.8 5.1 6.6 6.6l2.2-2.2c.3-.3.7-.4 1-.2 1.1.4 2.3.6 3.6.6.6 0 1 .4 1 1V20c0 .6-.4 1-1 1C10.6 21 3 13.4 3 4c0-.6.4-1 1-1h3.5c.6 0 1 .4 1 1 0 1.3.2 2.5.6 3.6.1.3 0 .7-.2 1z"/>
          </svg>
          <span>614-387-2259</span>
        </li>
        <li>
          <span class="contact-icon contact-icon--at">@</span>
          <span>KateBrook@klbarrowvista.com</span>
        </li>
      </ul>
    </div>
  </section>

  <section class="card card--back" aria-label="Card back">
    <span class="brand-mark"></span>
    <p class="wordmark">KL Barrow Vista</p>
    <p class="back-email">KateBrook@klbarrowvista.com</p>
  </section>
</main>
</body>
</html>
```